New Bicycle shop business card

Hi!
I'm looking for a business card for my new proffesional bike mechanics shop. This shop is only for fixing broken bikes and not selling bikes.
Peferbly a modern and sleek and modern design.
Colors: black, grey, red, white
Information:
Name: Rijwielwerkplaats Vanhoutte
Shop owner: Bart Vanhoutte & Marieke Segers
Website: www.rijwielwerkplaats-vanhoutte.be
Email: info@rijwielwerkplaats-vanhoutte.be
Phone number: +32471902368
Street adres: Kerkweg 46
9940 Bellebeke
Slogan/shop information: Herstellingen van alle merken.
Logo: see files.
Target Market(s)
People who seek a mechanic to fix or upgrade their bikes.
Contact Information for Business Card
Information:
Website: info@rijwielwerkplaats-vanhoutte.be
9940 Bellebeke
Logo: see files.

```html
<!DOCTYPE html>
<html lang="nl">
<head>
<meta charset="utf-8">
<title>Rijwielwerkplaats Vanhoutte – visitekaartje</title>
<link rel="stylesheet" href="https://fonts.googleapis.com/css2?family=Open+Sans:ital,wght@0,400;0,600;0,700;0,800;1,400&display=swap">
<style>
  :root {
    --red: #e31e2b;
    --black: #0b0b0c;
    --ink: #111111;
    --grey: #8a8a8a;
    --grey-light: #a3a3a3;
    --white: #ffffff;
    --stage: #d9d6d3;
    --pattern: #151516;
  }
  * { box-sizing: border-box; margin: 0; padding: 0; }
  html, body { width: 1200px; height: 716px; overflow: hidden; }
  body {
    background: var(--stage);
    font-family: "Open Sans", Arial, sans-serif;
    position: relative;
  }
  .card {
    position: absolute;
    top: 203px;
    width: 540px;
    height: 310px;
    overflow: hidden;
    box-shadow: 0 10px 28px rgba(0,0,0,.28);
  }

  /* Front */
  .card-front { left: 40px; background: var(--black); }
  .front-pattern {
    position: absolute; inset: 0;
    background: linear-gradient(135deg, var(--pattern), var(--black) 60%, var(--pattern));
  }
  .front-brand {
    position: absolute; left: 0; right: 0; top: 112px;
    display: flex; align-items: center; justify-content: center; gap: 12px;
  }
  .brand-dot {
    width: 26px; height: 26px; border-radius: 50%;
    background: var(--red); flex: none;
  }
  .brand-name {
    font-weight: 800; font-size: 22px; letter-spacing: .5px;
    text-transform: uppercase;
  }
  .front-brand .brand-name { color: var(--white); }
  .front-slogan {
    position: absolute; left: 0; right: 0; top: 196px;
    text-align: center; color: var(--white);
    font-size: 12px; font-weight: 400;
  }

  /* Back */
  .card-back { left: 620px; background: var(--white); }
  .owner { position: absolute; left: 30px; top: 30px; }
  .owner-label { color: var(--red); font-size: 12px; font-weight: 600; }
  .owner-names { color: var(--grey); font-size: 14px; font-weight: 700; margin-top: 2px; }
  .contact { position: absolute; left: 30px; top: 100px; }
  .company { color: var(--red); font-size: 15px; font-weight: 800; }
  .role { color: var(--ink); font-size: 11px; font-weight: 400; margin-bottom: 8px; }
  .contact-list { list-style: none; }
  .contact-list li {
    display: flex; align-items: center; gap: 7px;
    color: var(--grey-light); font-size: 11px; line-height: 18px;
  }
  .contact-list svg { width: 10px; height: 10px; flex: none; }
  .back-brand {
    position: absolute; right: 26px; top: 116px;
    display: flex; align-items: center; gap: 8px;
  }
  .back-brand .brand-name { color: var(--ink); font-size: 13px; }
  .back-brand .brand-dot { width: 18px; height: 18px; }
  .footer-band {
    position: absolute; left: 0; bottom: 0; height: 58px; width: 100%;
    background: var(--red);
    display: flex; align-items: center; padding-left: 30px;
  }
  .footer-band address {
    font-style: normal; color: var(--white); font-size: 12px; font-weight: 400;
  }
  .footer-corner {
    position: absolute; right: 0; bottom: 0; width: 120px; height: 58px;
    background: var(--black);
    display: flex; align-items: center; justify-content: center;
  }
  .footer-corner .brand-dot { width: 34px; height: 34px; }
</style>
</head>
<body>

<section class="card card-front" aria-label="Voorkant visitekaartje">
  <div class="front-pattern" role="img" aria-label="Donker herhalend patroon van het merkteken"></div>
  <div class="front-brand">
    <span class="brand-dot"></span>
    <span class="brand-name">Rijwielwerkplaats Vanhoutte</span>
  </div>
  <p class="front-slogan">Herstellingen van alle merken.</p>
</section>

<section class="card card-back" aria-label="Achterkant visitekaartje">
  <div class="owner">
    <p class="owner-label">Shop owner:</p>
    <p class="owner-names">Bart Vanhoutte &amp; Marieke Segers</p>
  </div>

  <div class="contact">
    <p class="company">Rijwielwerkplaats Vanhoutte</p>
    <p class="role">General Manager</p>
    <ul class="contact-list">
      <li>
        <svg viewBox="0 0 10 10" aria-hidden="true"><path d="M2 1l2 2-1 1c.5 1.2 1.3 2 2.5 2.5l1-1 2 2-1.3 1.3C4.5 8.5 1.5 5.5 1 2.3z" fill="var(--red)"/></svg>
        +32471902368
      </li>
      <li>
        <svg viewBox="0 0 10 10" aria-hidden="true"><rect x=".5" y="2" width="9" height="6" fill="var(--red)"/><path d="M.5 2l4.5 3.5L9.5 2" stroke="#fff" stroke-width=".9" fill="none"/></svg>
        info@rijwielwerkplaats-vanhoutte.be
      </li>
      <li>
        <svg viewBox="0 0 10 10" aria-hidden="true"><circle cx="5" cy="5" r="4.5" fill="var(--red)"/><path d="M.5 5h9M5 .5c-2 2.5-2 6.5 0 9M5 .5c2 2.5 2 6.5 0 9" stroke="#fff" stroke-width=".7" fill="none"/></svg>
        www.rijwielwerkplaats-vanhoutte.be
      </li>
    </ul>
  </div>

  <div class="back-brand">
    <span class="brand-dot"></span>
    <span class="brand-name">Rijwielwerkplaats Vanhoutte</span>
  </div>

  <div class="footer-band">
    <address>Kerkweg 46 9940 Bellebeke</address>
  </div>
  <div class="footer-corner">
    <span class="brand-dot"></span>
  </div>
</section>

</body>
</html>
```